Business Card for Industrial Distributor

We need a business card design for an industrial distributor. We sell machine parts for the manufacturing and oil industry. We would like the cards to look clean and modern but with a touch of industry.

Our colors are blue/white.

Please feel free to visit our website www.korvelpartsco.com

Target Market(s)

mexican manufacturers in the automobile/aerospace industry

Industry/Entity Type

Industrial

Colors
ffffff
0555a3

```html
<!DOCTYPE html>
<html lang="en">
<head>
<meta charset="utf-8">
<title>Korvel Parts – Business Card</title>
<link href="https://fonts.googleapis.com/css2?family=Montserrat:wght@400;500;600;700&display=swap" rel="stylesheet">
<style>
  :root{
    --bg:#e9ebee;
    --white:#ffffff;
    --navy:#2b3990;
    --text-blue:#1c5fae;
    --brand-blue:#1a75bc;
    --shadow:rgba(0,0,0,.35);
  }
  *{box-sizing:border-box;margin:0;padding:0}
  html,body{width:1200px;height:843px;overflow:hidden}
  body{background:var(--bg);position:relative;font-family:"Montserrat",sans-serif}
  .card{
    position:absolute;top:251px;width:536px;height:320px;
    border-radius:16px;overflow:hidden;
    box-shadow:3px 5px 6px var(--shadow);
  }
  .card--front{left:40px;background:var(--white)}
  .card--back{left:625px;background:var(--brand-blue)}
  .card__shapes{position:absolute;inset:0}

  .brand{position:absolute;left:31px;top:36px;display:flex;align-items:center;gap:12px}
  .brand__dot{width:56px;height:56px;border-radius:50%;background:var(--navy)}
  .brand__name{font-weight:700;font-size:36px;color:var(--navy);letter-spacing:-.5px}

  .side-tab{position:absolute;left:0;top:138px;width:20px;height:160px;background:var(--navy);border-radius:0 14px 14px 0}

  .contact{position:absolute;left:32px;top:145px;color:var(--text-blue)}
  .contact__name{font-size:21px;font-weight:600;color:var(--navy);line-height:1.2}
  .contact__role{font-size:13.5px;line-height:1.2;margin-bottom:10px}
  .contact__address{font-size:13.5px;line-height:1.4;font-style:normal;margin-bottom:10px}
  .contact__list{list-style:none;font-size:13.5px;line-height:1.32}
  .contact__list li{display:flex;align-items:center;gap:8px}
  .contact__list svg{width:10px;height:10px;fill:var(--navy);flex:none}
  .contact__list strong{font-weight:600;color:var(--navy)}

  .back-brand{position:absolute;left:196px;top:105px;width:168px;display:flex;flex-direction:column;align-items:center;gap:10px}
  .back-brand__dot{width:72px;height:72px;border-radius:50%;background:var(--white)}
  .back-brand__name{font-weight:700;font-size:22px;color:var(--white)}
  .back-web{position:absolute;left:0;right:0;top:274px;text-align:center;padding-left:290px;padding-right:0;color:var(--white);font-size:16.5px}
  .back-web{padding-left:0;left:160px;width:240px}
  .back-web strong{font-weight:600}
</style>
</head>
<body>

<section class="card card--front">
  <svg class="card__shapes" viewBox="0 0 536 320" aria-hidden="true">
    <circle cx="504" cy="126" r="125" fill="var(--navy)"/>
  </svg>

  <div class="brand">
    <span class="brand__dot"></span>
    <span class="brand__name">Korvel Parts</span>
  </div>

  <div class="side-tab"></div>

  <div class="contact">
    <p class="contact__name">Marcus Hale</p>
    <p class="contact__role">Director</p>
    <address class="contact__address">P.O. Box 3187<br>Lakeview, M I 48850</address>
    <ul class="contact__list">
      <li><svg viewBox="0 0 10 10"><path d="M2 0.5l1.6 2.2-1 1a6 6 0 0 0 3.7 3.7l1-1L9.5 8 8.3 9.5C4 9.5 .5 6 .5 1.7z"/></svg>+330 5182-4039</li>
      <li><svg viewBox="0 0 10 10"><path d="M0.5 2h9v6h-9zM1.5 3v.3L5 5.6 8.5 3.3V3zM1.5 4.5V7h7V4.5L5 6.8z" fill-rule="evenodd"/></svg>info@korvelpartsco.com</li>
      <li><svg viewBox="0 0 10 10"><path d="M5 .5a4.5 4.5 0 1 0 0 9 4.5 4.5 0 0 0 0-9zm0 1c.6 0 1.2 1.3 1.4 3H3.6C3.8 2.8 4.4 1.5 5 1.5zM1.6 5.5h1.9c.1 1 .3 1.9.7 2.6A3.5 3.5 0 0 1 1.6 5.5zm0-1a3.5 3.5 0 0 1 2.6-2.6c-.4.7-.6 1.6-.7 2.6zm3.4 4c-.6 0-1.2-1.3-1.4-3h2.8c-.2 1.7-.8 3-1.4 3zm.8-.4c.4-.7.6-1.6.7-2.6h1.9a3.5 3.5 0 0 1-2.6 2.6zm.7-3.6c-.1-1-.3-1.9-.7-2.6a3.5 3.5 0 0 1 2.6 2.6z"/></svg>www.<strong>korvelpartsco</strong>.com</li>
    </ul>
  </div>
</section>

<section class="card card--back">
  <svg class="card__shapes" viewBox="0 0 536 320" aria-hidden="true">
    <circle cx="-9" cy="160" r="162" fill="var(--white)"/>
  </svg>

  <div class="back-brand">
    <span class="back-brand__dot"></span>
    <span class="back-brand__name">Korvel Parts</span>
  </div>

  <p class="back-web">www.<strong>korvelpartsco</strong>.com</p>
</section>

</body>
</html>
```